Veltrano.co - Polar Expeditions Specialists

We need a modern, visually striking business card for Veltrano.co, a company specialized in selling expedition cruises to the most remote regions on Earth, with a focus on the Arctic and Antarctica. The design should instantly communicate that the cardholder is an expert in polar travel. Use clean, premium aesthetics with cool tones like icy blue and white, possibly incorporating polar imagery (ice, glaciers, penguins, etc.)

Attached the logo

Contact Information for Business Card

Feels high-end and trustworthy.. Visually memorable — encourages people to keep it

Colors
0054AA
0677BA
7BADD7
CADEEF
E8F1F8

Requirements
Must have
• ice, glaciers, penguins, montains
Nice to have
• modern, transparente,

```html
<!DOCTYPE html>
<html lang="en">
<head>
<meta charset="utf-8">
<title>Veltrano.co Business Card</title>
<link href="https://fonts.googleapis.com/css2?family=Arimo:wght@400;700&display=swap" rel="stylesheet">
<style>
  :root {
    --bg: #3d3d3d;
    --brand-blue: #3474b6;
    --deep-blue: #0054aa;
    --ice-blue: #7badd7;
    --frost: #5ad8f5;
    --white: #ffffff;
    --edge-grey: #9a9a9a;
    --card-radius: 18px;
  }
  * { margin: 0; padding: 0; box-sizing: border-box; }
  html, body {
    width: 1200px; height: 803px; overflow: hidden;
    background: var(--bg);
    font-family: "Arimo", Arial, sans-serif;
  }
  .stage {
    width: 1200px; height: 803px;
    display: flex; align-items: center; justify-content: center; gap: 40px;
  }
  .card {
    position: relative;
    width: 520px; height: 297px;
    border-radius: var(--card-radius);
    overflow: hidden;
  }
  .card-front { background: var(--white); }
  .front-panel {
    position: absolute; inset: 0;
    width: 100%; height: 100%;
  }
  .brand {
    position: absolute; left: 28px; top: 146px;
    display: flex; align-items: center; gap: 10px;
  }
  .brand-dot {
    width: 36px; height: 36px; border-radius: 50%;
    background: var(--brand-blue);
    flex: none;
  }
  .brand-name {
    font-weight: 700; font-size: 28px; color: var(--brand-blue);
    line-height: 1; white-space: nowrap;
  }
  .brand-tagline {
    margin-top: 4px;
    font-size: 10px; color: var(--brand-blue);
    white-space: nowrap;
  }
  .contact {
    position: absolute; right: 30px; top: 34px;
    text-align: right; color: var(--white);
  }
  .contact-name { font-weight: 700; font-size: 22px; line-height: 1.1; }
  .contact-title { font-size: 12px; margin-bottom: 16px; }
  .contact-address { font-size: 13px; line-height: 1.35; margin-bottom: 14px; }
  .contact-line {
    display: flex; justify-content: flex-end; align-items: center; gap: 8px;
    font-size: 13px; line-height: 1.55;
  }
  .contact-line svg { width: 12px; height: 12px; flex: none; }
  .card-back {
    background: linear-gradient(115deg, #1f4aa8 0%, var(--brand-blue) 45%, #45a6e0 75%, var(--frost) 100%);
  }
</style>
</head>
<body>
<main class="stage">
  <section class="card card-front" aria-label="Business card front">
    <svg class="front-panel" viewBox="0 0 520 297" aria-hidden="true">
      <path d="M335 -10 Q270 90 273 170 Q277 250 335 310 L530 310 L530 -10 Z" fill="var(--edge-grey)" transform="translate(-6 0)"/>
      <path d="M335 -10 Q270 90 273 170 Q277 250 335 310 L530 310 L530 -10 Z" fill="var(--brand-blue)"/>
    </svg>
    <div class="brand">
      <div class="brand-dot"></div>
      <div>
        <div class="brand-name">Veltrano.co</div>
        <div class="brand-tagline">Polar Expeditions Specialists</div>
      </div>
    </div>
    <div class="contact">
      <div class="contact-name">Marcus Hale</div>
      <div class="contact-title">President</div>
      <div class="contact-address">4512 Glacier Bay Road<br>Northport, Canada 20817</div>
      <div class="contact-line">555-210-4478
        <svg viewBox="0 0 12 12"><path d="M2.5 1 L4.5 1 L5.2 3.5 L4 4.5 Q5 7 7.5 8 L8.5 6.8 L11 7.5 L11 9.5 Q10.5 11 9 11 Q1 10 1 3 Q1 1.5 2.5 1 Z" fill="var(--white)"/></svg>
      </div>
      <div class="contact-line">555-390-6612
        <svg viewBox="0 0 12 12"><rect x="3" y="0.8" width="6" height="10.4" rx="1" fill="none" stroke="var(--white)" stroke-width="1.2"/></svg>
      </div>
      <div class="contact-line">info@veltrano.com
        <svg viewBox="0 0 12 12"><rect x="0.5" y="2.5" width="11" height="7.5" fill="var(--white)"/><path d="M0.5 2.5 L6 7 L11.5 2.5" fill="none" stroke="var(--brand-blue)" stroke-width="1"/></svg>
      </div>
      <div class="contact-line">www.veltrano.com
        <svg viewBox="0 0 12 12"><circle cx="6" cy="6" r="5" fill="none" stroke="var(--white)" stroke-width="1.2"/><path d="M1 6 H11 M6 1 Q3 6 6 11 M6 1 Q9 6 6 11" fill="none" stroke="var(--white)" stroke-width="0.9"/></svg>
      </div>
    </div>
  </section>

  <section class="card card-back" role="img" aria-label="Repeating pattern of the brand's polar animal mark in shades of blue fading to icy cyan"></section>
</main>
</body>
</html>
```